Biz Card

MARKETING today is the most rapidly changing business discipline. Media options to reach customers, actual customer preferences and consumer buying decisions change by the minute . . . no, by the second. The behavioral data generated by all aspects of the business and the new technologies that put the data to work together produce the potential to generate business intelligence and guide smart resource allocation to influence purchase and retention. However, to realize this potential, marketing professionals at all levels and in all organizations must continuously improve their skills not just from on-the-job training but by learning from masters in the field. The Bright Horizon Guild is the training center that serves this professional development need.model logos:msi.orgama.orgcontentmarketinginstitute.comBook covers on MarketingMetrics, Marketing Anaytics
Industry/Entity Type
Business
Contact Information for Business Card
Roy A. YoungCEOMarketing Science Academyphone: 310-601-4755email: roy@marketingscience.comAddress:437 South Rexford DriveBeverly Hills, CA 89377
Look and feel
Each slider illustrates characteristics of the customer's brand and the style your logo design should communicate.

```html
<!DOCTYPE html>
<html lang="en">
<head>
<meta charset="utf-8">
<title>Bright Horizon Guild – Business Card</title>
<link href="https://fonts.googleapis.com/css2?family=Jost:wght@400;500&display=swap" rel="stylesheet">
<style>
  :root {
    --brand-blue: #1350a4;
    --brand-green: #a2bf3c;
    --ink-white: #ffffff;
    --backdrop: #5c5c5c;
  }
  * { margin: 0; padding: 0; box-sizing: border-box; }
  html, body {
    width: 1200px; height: 900px; overflow: hidden;
    background: var(--backdrop);
    font-family: "Jost", sans-serif;
    color: var(--ink-white);
  }
  .card {
    position: absolute;
    width: 700px; height: 400px;
    background: var(--brand-blue);
    overflow: hidden;
    box-shadow: 0 6px 18px rgba(0,0,0,0.35);
  }
  .card--front { left: 60px; top: 40px; }
  .card--back { left: 440px; top: 470px; }

  .card__bands { position: absolute; inset: 0; }

  .holder { position: absolute; left: 48px; top: 38px; }
  .holder__name { font-size: 23px; font-weight: 400; letter-spacing: 0.5px; }
  .holder__title { font-size: 18px; margin-top: 2px; }

  .brand { position: absolute; left: 215px; top: 140px; display: flex; align-items: center; gap: 22px; }
  .brand__square { width: 86px; height: 86px; background: var(--ink-white); }
  .brand__name { font-size: 34px; font-weight: 500; line-height: 0.95; }

  .contact { position: absolute; left: 60px; top: 300px; font-size: 21px; letter-spacing: 0.4px; }
  .contact__row { display: flex; gap: 40px; margin-top: 6px; }

  .tagline {
    position: absolute; left: 185px; top: 130px;
    padding-left: 22px;
    border-left: 8px solid var(--brand-green);
    font-size: 29px; font-weight: 500; line-height: 1.02; letter-spacing: 0.5px;
  }
  .website { position: absolute; left: 215px; top: 262px; font-size: 18px; letter-spacing: 1px; }
</style>
</head>
<body>

<section class="card card--front">
  <svg class="card__bands" width="700" height="400" viewBox="0 0 700 400" aria-hidden="true">
    <polygon points="0,125 200,125 150,290 0,290" fill="var(--brand-green)"/>
    <polygon points="570,200 700,200 700,360 520,360" fill="var(--brand-green)"/>
  </svg>

  <div class="holder">
    <p class="holder__name">Neil P. Barton</p>
    <p class="holder__title">CEO</p>
  </div>

  <div class="brand">
    <span class="brand__square"></span>
    <p class="brand__name">Bright<br>Horizon<br>Guild</p>
  </div>

  <div class="contact">
    <p>912 North Calloway Lane, Beverly Hills, CA 89377</p>
    <p class="contact__row"><span>neil@brighthorizonguild.com</span><span>310-555-0182</span></p>
  </div>
</section>

<section class="card card--back">
  <p class="tagline">Executive Education<br>in Marketing Analytics<br>and Technology</p>
  <p class="website">www.brighthorizonguild.com</p>
</section>

</body>
</html>
```